Wordpress website for a new Podcast

Hi, We are looking for a designer to create a wordpress website project for a new podcast and publish it on the domain we own.

The show is called “Bright Gatherings” (logo included) and its aim is to interview guests who work as professional facilitators, trainers, teachers and coaches. The show has a positive vibe, is fun, vibrant and full of positive energy. These are the feelings we want to convey in the design.

The website should have a similar structure to: https://www.plumvesselcast.example/ with the following content:

1) The main page including:
- navigation bar and social buttons at the top
- main graphic design featuring the latest episode
- "latest episodes" section displaying 3 episodes (please design a mask to be used for new episodes when they air together with the face of the interviewee) -> this will link to the respective episodes
- please design an "bright gatherings" book cover mockup to be inluded as a banner -> this will link to Orindel
- subscribe to the newsletter - a banner capturing the name and email of the user -> to be connected to PostWren.
-> a working episode search.

2) Episodes page
- the show will be divided into seasons (12 episodes each) and each episode will need a separate "blog entry" including:
-> A short article (4-5 paragraphs) + stock image
-> interviewee's bio and social links

3) Meet the hosts page
- including bios of the two hosts of the show
- links to their social profiles
- a "request speaker availability" form which sends an email

Some additional nice-to-haves:
1) Good and clean Bio's would be awesome (both for the hosts & the interviewees),
2) an easily navigable episode system,
3) a keyword/date search option
4) easy to share options (share to WhatsApp, Facebook, Twitter, LinkedIn) 5) We must be able to track how the podcasts are shared (google analytics?)

```html
<!DOCTYPE html>
<html lang="en">
<head>
<meta charset="utf-8">
<title>Bright Gatherings — Podcast</title>
<link href="https://fonts.googleapis.com/css2?family=Montserrat:wght@300;400;500;600;700;800&family=Roboto+Condensed:wght@400&display=swap" rel="stylesheet">
<style>
:root{
  --orange:#f4511e;
  --red:#e8401a;
  --yellow:#f5b21b;
  --dark:#141414;
  --ink:#222;
  --muted:#555;
  --light:#f4f4f4;
  --card:#f2f2f2;
  --footer:#1d1d1d;
  --white:#fff;
}
*{box-sizing:border-box;margin:0;padding:0}
html,body{width:1200px;height:5038px;overflow:hidden}
body{position:relative;background:var(--light);font-family:"Montserrat",sans-serif;color:var(--ink)}
.abs{position:absolute}
.btn{position:absolute;display:flex;align-items:center;justify-content:center;font-weight:700;font-size:14px;color:var(--white);text-transform:uppercase;border-radius:2px}
.btn-red{background:var(--red)}
.btn-yellow{background:var(--yellow);color:#2a1a00}

/* header */
.site-header{left:0;top:0;width:1200px;height:131px;background:var(--orange);z-index:5}
.brand{left:128px;top:-6px;width:154px;height:154px;border-radius:50%;background:var(--orange);display:flex;align-items:center;justify-content:center;text-align:center;color:var(--white);font-weight:800;font-size:20px;line-height:1.1;z-index:6}
.question{left:434px;top:22px;color:var(--white);font-size:12px}
.phone-num{left:390px;top:38px;color:var(--white);font-size:23px;font-weight:700}
.icon-circle{position:absolute;width:38px;height:38px;border:2px solid var(--white);border-radius:50%;display:flex;align-items:center;justify-content:center}
.nav{left:328px;top:90px;display:flex;gap:27px;color:var(--white);font-size:15px;font-weight:700}

/* hero */
.hero{left:0;top:131px;width:1200px;height:700px}
.hero-title{left:620px;top:310px;color:var(--white);font-size:47px;font-weight:700}
.hero-text{left:620px;top:383px;width:400px;color:#ccc;font-size:17px;line-height:34px}
.slider-arrow{position:absolute;width:36px;height:36px;border-radius:50%;background:rgba(255,255,255,.12);display:flex;align-items:center;justify-content:center}
.book{left:143px;top:264px;width:381px;height:592px}
.book-cover{position:absolute;left:0;top:0;width:356px;height:592px;background:radial-gradient(circle at 50% 60%,#ffd21f 0%,#fb9a12 40%,#f2451a 80%);box-shadow:6px 10px 22px rgba(0,0,0,.35);display:flex;justify-content:center;padding-top:96px;font-size:52px;font-weight:800;color:#1a1a1a;text-align:center;line-height:1.05}
.book-pages{position:absolute;left:356px;top:14px;width:22px;height:570px;background:linear-gradient(90deg,#ddd,#fff,#cfcfcf)}

/* intro */
.intro-title{left:143px;top:964px;width:440px;font-family:"Roboto Condensed",sans-serif;font-size:28px;line-height:42px;color:#1a1a1a}
.intro-text{left:143px;top:1112px;width:440px;font-size:13.5px;line-height:31.5px;color:var(--muted)}
.emblem{left:600px;top:952px;width:110px;height:426px;background:linear-gradient(180deg,#ececec,#dedede);border-radius:4px}
.feature-icon{position:absolute;left:758px;width:82px;height:82px;border-radius:50%;background:var(--orange);border:4px solid #fbd2c2;display:flex;align-items:center;justify-content:center}
.feature-title{position:absolute;left:857px;font-size:18px;line-height:30px;font-weight:500;color:#1a1a1a;text-transform:uppercase}
.feature-text{position:absolute;left:758px;width:300px;font-size:12px;line-height:24px;color:var(--muted)}

/* trainers */
.trainers-photo{left:0;top:1475px;width:1200px;height:735px}
.kicker{position:absolute;color:var(--white);font-weight:300}
.big-title{position:absolute;color:var(--white);font-weight:800;text-transform:uppercase}
.section-text{position:absolute;width:400px;color:#ddd;font-size:17px;line-height:34px}
.video{left:143px;top:1993px;width:912px;height:459px;border:6px solid var(--white);box-shadow:0 12px 30px rgba(0,0,0,.25);background:linear-gradient(135deg,#d9dde0 0%,#a9b1b8 45%,#3f4b5a 100%)}
.play{left:415px;top:203px;width:82px;height:48px;border-radius:10px;background:#e1251b;display:flex;align-items:center;justify-content:center}

/* episodes */
.section-heading{left:0;top:2548px;width:1200px;text-align:center;font-size:38px;color:#111}
.section-heading b{font-weight:800}
.section-heading span{font-weight:300}
.heading-rule{left:561px;top:2620px;width:78px;height:3px;background:var(--red)}
.episode{position:absolute;top:2677px;width:285px;height:486px;background:var(--card)}
.episode-photo{height:183px}
.episode-badge{position:absolute;left:121px;top:168px;width:44px;height:44px;border-radius:50%;background:var(--red);border:3px solid var(--white);display:flex;align-items:center;justify-content:center}
.episode-num{position:absolute;top:224px;width:100%;text-align:center;color:var(--red);font-size:15px}
.episode-title{position:absolute;top:253px;width:100%;text-align:center;font-weight:600;font-size:15px;line-height:23px;color:#1a1a1a}
.episode-text{position:absolute;top:307px;left:16px;right:16px;text-align:center;font-size:12px;line-height:25.5px;color:var(--muted)}
.episode .btn{left:86px;top:428px;width:112px;height:30px;font-size:11px}

/* hosts */
.hosts-photo{left:0;top:3283px;width:1200px;height:700px}

/* newsletter */
.newsletter-band{left:0;top:3880px;width:1200px;height:440px}
.newsletter-title{left:0;top:4014px;width:1200px;text-align:center;color:var(--white);font-size:36px;font-weight:800;text-transform:uppercase}
.newsletter-sub{left:0;top:4080px;width:1200px;text-align:center;color:#ffe3d8;font-size:16px}
.field{position:absolute;top:4142px;height:40px;border-radius:20px;background:var(--white);font-size:11px;color:#888;padding-left:20px;display:flex;align-items:center}
.subscribe{left:817px;top:4142px;width:157px;height:40px;border-radius:20px;background:#111;font-size:14px}

/* testimonial */
.avatar{left:186px;top:4414px;width:180px;height:180px;border-radius:50%;border:3px solid var(--red);padding:6px;background:var(--white)}
.avatar div{width:100%;height:100%;border-radius:50%;background:linear-gradient(160deg,#8fa4b8,#3d5368)}
.quote-mark{left:372px;top:4380px;font-size:90px;font-weight:800;color:#ccc;line-height:1}
.quote-title{left:432px;top:4420px;width:450px;font-size:17px;line-height:31px;font-weight:600;color:#1a1a1a}
.stars{left:432px;top:4486px;display:flex;gap:3px;align-items:center}
.quote-date{margin-left:14px;font-size:14px;color:#333}
.quote-text{left:432px;top:4522px;width:590px;font-size:12.5px;line-height:25.5px;color:var(--muted)}

/* footer */
.site-footer{left:0;top:4719px;width:1200px;height:319px;background:var(--footer);color:var(--white);text-align:center}
.footer-contacts{position:absolute;top:70px;width:100%;display:flex;justify-content:center;gap:36px;font-size:15px}
.footer-contacts span{display:flex;align-items:center;gap:10px}
.footer-links{position:absolute;top:118px;width:100%;font-size:15px}
.copyright{position:absolute;top:164px;width:100%;font-size:15px}
.footer-social{position:absolute;top:213px;left:0;width:100%;display:flex;justify-content:center;gap:14px}
.footer-social i{width:36px;height:36px;border-radius:50%;border:2px solid var(--red);display:block}
</style>
</head>
<body>

<header class="abs site-header">
  <div class="abs brand">Bright<br>Gatherings</div>
  <div class="abs question">Have any Question?</div>
  <div class="abs phone-num">(07) 5550 1842</div>
  <div class="icon-circle" style="left:576px;top:23px">
    <svg width="16" height="16" viewBox="0 0 24 24" fill="#fff"><path d="M6.6 10.8a15.1 15.1 0 006.6 6.6l2.2-2.2c.3-.3.7-.4 1-.2 1.1.4 2.3.6 3.6.6.6 0 1 .4 1 1V20c0 .6-.4 1-1 1A17 17 0 013 4c0-.6.4-1 1-1h3.5c.6 0 1 .4 1 1 0 1.3.2 2.5.6 3.6.1.3 0 .7-.2 1z"/></svg>
  </div>
  <div class="icon-circle" style="left:634px;top:23px">
    <svg width="16" height="16" viewBox="0 0 24 24" fill="none" stroke="#fff" stroke-width="3"><circle cx="10" cy="10" r="7"/><path d="M15 15l6 6"/></svg>
  </div>
  <div class="icon-circle" style="left:690px;top:23px" aria-label="Social profile"></div>
  <div class="icon-circle" style="left:734px;top:23px" aria-label="Social profile"></div>
  <div class="icon-circle" style="left:778px;top:23px" aria-label="Social profile"></div>
  <div class="btn btn-yellow" style="left:840px;top:20px;width:215px;height:42px">Get the book now</div>
  <nav class="abs nav"><span>HOME</span><span>ABOUT</span><span>EPISODES</span><span>MEET THE HOSTS</span><span>TRAININGS</span><span>HOP</span><span>CONTACT US</span></nav>
</header>

<section class="abs hero">
  <svg class="abs" style="left:0;top:0" width="1200" height="700"><defs><linearGradient id="heroBg" x1="0" y1="0" x2="1" y2="1"><stop offset="0" stop-color="#1b1b1b"/><stop offset="1" stop-color="#0c0c0c"/></linearGradient></defs><polygon points="0,0 1200,0 1200,688 0,553" fill="url(#heroBg)"/></svg>
  <div class="abs hero-title" style="top:179px">Bright Gatherings</div>
  <p class="abs hero-text" style="top:252px">Sed ut perspiciatis unde omnis iste natus sit voluptatem accusantium doloremque laudantium, totam rem aperiam</p>
  <div class="btn btn-red" style="left:620px;top:383px;width:201px;height:43px">Get the book now</div>
  <div class="btn btn-yellow" style="left:836px;top:383px;width:170px;height:43px">Get trained</div>
  <svg class="abs" style="left:562px;top:460px" width="90" height="80" viewBox="0 0 90 80" fill="none" stroke="#fff" stroke-width="3" stroke-linecap="round"><path d="M84 4c4 34-26 60-74 64"/><path d="M22 56L8 68l16 8"/></svg>
  <div class="slider-arrow" style="left:60px;top:292px"><svg width="12" height="12" viewBox="0 0 12 12" fill="none" stroke="#fff" stroke-width="2"><path d="M8 1L3 6l5 5"/></svg></div>
  <div class="slider-arrow" style="left:1102px;top:292px"><svg width="12" height="12" viewBox="0 0 12 12" fill="none" stroke="#fff" stroke-width="2"><path d="M4 1l5 5-5 5"/></svg></div>
</section>

<div class="abs book" role="img" aria-label="Bright Gatherings book cover mockup">
  <div class="book-cover">BRIGHT<br>GATHERINGS</div>
  <div class="book-pages"></div>
</div>

<section>
  <h2 class="abs intro-title" style="font-weight:400">What's Bright Gatherings You Can Do Such That By Doing It Everything Else Will Be Easier Or Unnecessary?</h2>
  <p class="abs intro-text">Sed ut perspiciatis unde omnis iste natus error sit voluptatem accusantium doloremque laudantium, totam rem aperiam, eaque ipsa quae ab illo inventore veritatis et quasi architecto beatae vitae dicta sunt explicabo. Nemo enim ipsam voluptatem quia voluptas sit aspernatur aut odit aut fugit</p>
  <div class="btn btn-red" style="left:143px;top:1295px;width:125px;height:40px;font-size:12px">Read more</div>
  <div class="abs emblem" role="img" aria-label="Bright Gatherings brand emblem"></div>

  <div class="feature-icon" style="top:953px"><svg width="40" height="40" viewBox="0 0 40 40" fill="none" stroke="#fff" stroke-width="2.5"><rect x="6" y="6" width="28" height="20"/><path d="M12 34v-8M28 34v-8M12 14h16M12 19h10"/></svg></div>
  <div class="feature-title" style="top:966px">Bright<br>Trainers</div>
  <p class="feature-text" style="top:1045px">Sed ut perspiciatis unde omnis iste natus ptatem accusantium doloremque laudantium, totam rem aperiam, eaque ipsa quae ab illo inventore veritatis et quasi architecto beatae vitae</p>

  <div class="feature-icon" style="top:1166px"><svg width="40" height="40" viewBox="0 0 40 40" fill="none" stroke="#fff" stroke-width="2.5"><rect x="5" y="7" width="30" height="20"/><circle cx="14" cy="17" r="4"/><path d="M22 14h8M22 20h6M10 34l4-7M30 34l-4-7"/></svg></div>
  <div class="feature-title" style="top:1174px">Teachers and<br>Coaches</div>
  <p class="feature-text" style="top:1254px">Sed ut perspiciatis unde omnis iste natus ptatem accusantium doloremque laudantium, totam rem aperiam, eaque ipsa quae ab illo inventore veritatis et quasi architecto beatae vitae</p>
</section>

<section>
  <svg class="abs trainers-photo" role="img" aria-label="Speaker addressing a large audience on stage" width="1200" height="735"><defs><radialGradient id="trainBg" cx="0.35" cy="0.35" r="0.8"><stop offset="0" stop-color="#3a4a66"/><stop offset="0.5" stop-color="#1b2233"/><stop offset="1" stop-color="#0c0f18"/></radialGradient></defs><polygon points="0,0 1200,0 1200,612 0,727" fill="url(#trainBg)"/></svg>
  <div class="kicker" style="left:659px;top:1552px;font-size:45px">Bright Gatherings</div>
  <div class="big-title" style="left:659px;top:1612px;font-size:47px">Trainers</div>
  <p class="section-text" style="left:659px;top:1684px">Sed ut perspiciatis unde omnis iste natus sit voluptatem accusantium doloremque laudantium, totam rem aperiam</p>
  <div class="btn btn-yellow" style="left:659px;top:1810px;width:171px;height:44px">Get trained</div>
  <div class="abs video" role="img" aria-label="Training session video with presenter and seated group">
    <div class="abs play"><svg width="20" height="22" viewBox="0 0 20 22"><path d="M2 1l17 10L2 21z" fill="#fff"/></svg></div>
  </div>
</section>

<section>
  <h2 class="abs section-heading"><b>LATEST</b> <span>PODCAST</span> <b>EPISODES</b></h2>
  <div class="abs heading-rule"></div>

  <article class="episode" style="left:143px">
    <div class="episode-photo" role="img" aria-label="Speaker raising arms before a crowd" style="background:linear-gradient(180deg,#6a6a72,#2b2122)"></div>
    <div class="episode-badge"><svg width="20" height="20" viewBox="0 0 20 20" fill="none" stroke="#fff" stroke-width="2"><circle cx="10" cy="8" r="2"/><path d="M6 12a5 5 0 118 0M3 15a8.5 8.5 0 1114 0"/></svg></div>
    <div class="episode-num">Episode 194:</div>
    <div class="episode-title">Nemo enim ipsam voluptatem<br>voluptas sit aspernatur</div>
    <p class="episode-text">Sed ut perspiciatis unde omnis iste natus error sit voluptatem accusantium doloremque laudantium, totam rem aperiam, eaque ipsa quae ab illo</p>
    <div class="btn btn-red">Explore</div>
  </article>

  <article class="episode" style="left:456px">
    <div class="episode-photo" role="img" aria-label="Presenter speaking to a seated group" style="background:linear-gradient(180deg,#c7c2b6,#4e5667)"></div>
    <div class="episode-badge"><svg width="20" height="20" viewBox="0 0 20 20" fill="none" stroke="#fff" stroke-width="2"><circle cx="10" cy="8" r="2"/><path d="M6 12a5 5 0 118 0M3 15a8.5 8.5 0 1114 0"/></svg></div>
    <div class="episode-num">Episode 194:</div>
    <div class="episode-title">Nemo enim ipsam voluptatem<br>voluptas sit aspernatur</div>
    <p class="episode-text">Sed ut perspiciatis unde omnis iste natus error sit voluptatem accusantium doloremque laudantium, totam rem aperiam, eaque ipsa quae ab illo</p>
    <div class="btn btn-red">Explore</div>
  </article>

  <article class="episode" style="left:770px">
    <div class="episode-photo" role="img" aria-label="Auditorium audience facing a lit stage" style="background:linear-gradient(180deg,#1f3b5e,#14202e)"></div>
    <div class="episode-badge"><svg width="20" height="20" viewBox="0 0 20 20" fill="none" stroke="#fff" stroke-width="2"><circle cx="10" cy="8" r="2"/><path d="M6 12a5 5 0 118 0M3 15a8.5 8.5 0 1114 0"/></svg></div>
    <div class="episode-num">Episode 194:</div>
    <div class="episode-title">Nemo enim ipsam voluptatem<br>voluptas sit aspernatur</div>
    <p class="episode-text">Sed ut perspiciatis unde omnis iste natus error sit voluptatem accusantium doloremque laudantium, totam rem aperiam, eaque ipsa quae ab illo</p>
    <div class="btn btn-red">Explore</div>
  </article>
</section>

<section>
  <div class="abs hosts-photo" role="img" aria-label="Host on stage facing an audience" style="background:radial-gradient(circle at 75% 40%,#5a4638 0%,#2a1d17 45%,#120d0b 100%)"></div>
  <div class="kicker" style="left:143px;top:3416px;font-size:30px">Bright Gatherings</div>
  <div class="big-title" style="left:143px;top:3466px;font-size:48px">Meet the hosts</div>
  <p class="section-text" style="left:143px;top:3540px">Sed ut perspiciatis unde omnis iste natus sit voluptatem accusantium doloremque laudantium, totam rem aperiam</p>
  <div class="btn btn-red" style="left:143px;top:3667px;width:316px;height:50px;font-size:14px">Request speaker availability</div>
</section>

<section>
  <svg class="abs newsletter-band" width="1200" height="440"><defs><linearGradient id="bandBg" x1="0" y1="0" x2="0" y2="1"><stop offset="0" stop-color="#f04d1d"/><stop offset="1" stop-color="#d8340f"/></linearGradient></defs><polygon points="0,8 1200,95 1200,350 0,438" fill="url(#bandBg)"/></svg>
  <h2 class="abs newsletter-title">Join our newsletter</h2>
  <p class="abs newsletter-sub">Quis autem vel eum iure reprehenderit qui in ea voluptate velit esse quam nihil</p>
  <div class="field" style="left:227px;width:275px">Name</div>
  <div class="field" style="left:522px;width:275px">Email address</div>
  <div class="btn subscribe">Subscribe</div>
</section>

<section>
  <div class="slider-arrow" style="left:115px;top:4502px;background:none"><svg width="18" height="30" viewBox="0 0 18 30" fill="none" stroke="#777" stroke-width="2.5"><path d="M15 2L3 15l12 13"/></svg></div>
  <div class="slider-arrow" style="left:1047px;top:4502px;background:none"><svg width="18" height="30" viewBox="0 0 18 30" fill="none" stroke="#777" stroke-width="2.5"><path d="M3 2l12 13L3 28"/></svg></div>
  <div class="abs avatar" role="img" aria-label="Portrait of a listener"><div></div></div>
  <div class="abs quote-mark">&ldquo;</div>
  <h3 class="abs quote-title">QUIS AUTEM VEL EUM IURE REPREHENDERIT QUI IN EA VOLUPTATE VELIT ESSE</h3>
  <div class="abs stars">
    <svg width="100" height="16" viewBox="0 0 100 16" fill="none" stroke="#e8401a" stroke-width="1.4"><g id="st"><path d="M8 1l2 5h5l-4 3 2 5-5-3-5 3 2-5-4-3h5z"/></g><use href="#st" x="20"/><use href="#st" x="40"/><use href="#st" x="60"/><use href="#st" x="80"/></svg>
    <span class="quote-date">January 3, 2019</span>
  </div>
  <p class="abs quote-text">Sed ut perspiciatis unde omnis iste natus error sit voluptatem accusantium doloremque laudantium, totam rem aperiam, eaque ipsa quae ab illo inventore veritatis et quasi architecto beatae vitae dicta sunt explicabo. Nemo enim ipsam voluptatem quia voluptas sit aspernatur aut odit aut fugit, sed quia consequuntur magni dolores</p>
</section>

<footer class="abs site-footer">
  <div class="footer-contacts">
    <span><svg width="12" height="16" viewBox="0 0 12 16"><path d="M6 0a6 6 0 00-6 6c0 4.5 6 10 6 10s6-5.5 6-10a6 6 0 00-6-6zm0 8.5A2.5 2.5 0 116 3.5a2.5 2.5 0 010 5z" fill="#e8401a"/></svg>Bright Gatherings, Larkfield, WA, 6099</span>
    <span><svg width="14" height="14" viewBox="0 0 24 24" fill="#e8401a"><path d="M6.6 10.8a15.1 15.1 0 006.6 6.6l2.2-2.2c.3-.3.7-.4 1-.2 1.1.4 2.3.6 3.6.6.6 0 1 .4 1 1V20c0 .6-.4 1-1 1A17 17 0 013 4c0-.6.4-1 1-1h3.5c.6 0 1 .4 1 1 0 1.3.2 2.5.6 3.6.1.3 0 .7-.2 1z"/></svg>(808) 555-0147</span>
    <span><svg width="16" height="12" viewBox="0 0 16 12"><rect width="16" height="12" rx="1" fill="#e8401a"/><path d="M1 1l7 6 7-6" stroke="#1d1d1d" stroke-width="1.5" fill="none"/></svg>hello@brightgatherings.example</span>
  </div>
  <div class="footer-links">Home &nbsp;|&nbsp; About Us &nbsp;|&nbsp; Episodes &nbsp;|&nbsp; Meet the hosts &nbsp;|&nbsp; Training &nbsp;|&nbsp; Shop &nbsp;|&nbsp; Contact Us</div>
  <div class="copyright">&copy; 2019 Bright Gatherings. All Rights Reserved.</div>
  <div class="footer-social"><i aria-label="Social profile"></i><i aria-label="Social profile"></i><i aria-label="Social profile"></i><i aria-label="Social profile"></i></div>
</footer>

</body>
</html>
```